Manuka Honey company needs a Upmarket, Luxury Website!

New Zealand, Taranaki based Manuka Honey company Rimu Vale Honey is looking for a new website, we are looking for an upmarket, luxury, serious website design. We export the highest quality quality Manuka Honey, straight from the Taranaki region.

Main export markets are Asia & Europe, also New Zealand & Australia.

Looking to have a beautiful, upmarket, serious, luxurious & graphical experience with mobile optimization in mind. Like the use of product staging/mockups

You can use copy from other websites to build the site and we will change the copy after the design is finished.

***Please include 'Honey Product' mockups in website.

*Will add illustrator files in coming days***

Feel free to make website functional in Shopify, Wordpress or WIX

Target Market(s)

Asia, Europe (main markets) New Zealand, Australia (Submarkets)

Coding

Coded - Design and coding required

Number of Pages Required

4 page

Requirements
Must have
• Home, Shop, About Us, Contact Us

Homepage to include:

Our Products
Company Video (video under construction)
What is MGO/KPS
Newsletter Opt-in

***(Not in Order)***

Please include 'Honey Product' mockups in website.
*Will add illustrator files in coming days
Nice to have
• FAQ & Partnership Inquiries (hyperlink in footer)

```html
<!DOCTYPE html>
<html lang="en">
<head>
<meta charset="utf-8">
<title>Rimu Vale Honey — Premium Mānuka Honey</title>
<link href="https://fonts.googleapis.com/css2?family=Roboto:wght@400;500;700&family=Montserrat:wght@400;500&display=swap" rel="stylesheet">
<style>
:root{
  --gold:#f2b705;
  --gold-deep:#e0a800;
  --ink:#111111;
  --text:#333333;
  --muted:#666666;
  --dark:#1e1e1e;
  --footer:#2a2a2a;
  --paper:#ffffff;
  --line:#e3e3e3;
}
*{box-sizing:border-box;margin:0;padding:0}
html,body{width:1200px;height:3771px;overflow:hidden}
body{position:relative;background:var(--paper);font-family:"Roboto",sans-serif;color:var(--text)}
.abs{position:absolute}
a{color:inherit;text-decoration:none}

/* header */
.site-header{position:absolute;left:0;top:0;width:1200px;height:76px;background:var(--dark)}
.main-nav{position:absolute;left:100px;top:29px;display:flex;align-items:center;gap:16px;color:#fff;font-size:14px;font-weight:500}
.main-nav .dot{width:5px;height:5px;border-radius:50%;background:#fff}
.brand{position:absolute;left:0;width:1200px;top:24px;text-align:center;font-family:"Montserrat",sans-serif;font-size:21px;letter-spacing:5px;color:var(--gold);font-weight:400}
.cart{position:absolute;left:1074px;top:24px}

/* hero */
.hero{position:absolute;left:0;top:76px;width:1200px;height:690px}
.hero-title{position:absolute;left:98px;top:184px;color:#fff;font-size:42px;font-weight:700;line-height:48px;text-align:center;white-space:nowrap;letter-spacing:-.3px;text-shadow:0 2px 6px rgba(0,0,0,.4)}
.hero-text{position:absolute;left:100px;top:289px;width:420px;color:#fff;font-size:14px;line-height:25px;text-shadow:0 1px 3px rgba(0,0,0,.4)}
.btn{display:flex;align-items:center;justify-content:center;background:var(--gold);color:#fff;font-weight:700;font-size:15px;letter-spacing:.3px}
.hero-btn{position:absolute;left:100px;top:348px;width:136px;height:41px;border:2px solid #fff3}

/* featured */
.section-title{position:absolute;left:0;width:1200px;text-align:center;color:var(--ink);font-weight:700}
.card{position:absolute;top:1010px;width:318px;height:216px;background:#fff;border:3px solid #f1f5fb;box-shadow:0 2px 8px rgba(0,0,0,.04)}
.card .name{position:absolute;top:116px;left:0;width:100%;text-align:center;font-weight:500;font-size:16px;color:var(--ink)}
.card .price{position:absolute;top:140px;left:0;width:100%;text-align:center;font-weight:500;font-size:16px;color:var(--ink)}
.card .stars{position:absolute;top:166px;left:0;width:100%;text-align:center;color:var(--gold);font-size:20px;letter-spacing:1px}
.jar{position:absolute;border-radius:14px}

/* mgo table */
.kps-table{position:absolute;left:136px;top:2308px;width:400px;font-size:15px;color:var(--ink)}
.kps-row{position:absolute;left:0;width:380px;height:44px}
.kps-row .lvl{position:absolute;left:2px;font-weight:500}
.kps-row .use{position:absolute;left:103px;font-size:11px;line-height:16px;color:#444}
.kps-row .mgo{position:absolute;left:231px;color:var(--gold);font-size:15px}
.kps-row .kps{position:absolute;left:336px;font-weight:700;font-size:18px}
.kps-row.rule{border-bottom:1px solid var(--line)}

footer{position:absolute;left:0;top:3505px;width:1200px;height:266px;background:var(--footer)}
.foot-nav a{position:absolute;top:104px;color:var(--gold);font-size:14px;font-weight:500;transform:translateX(-50%)}
</style>
</head>
<body>

<header class="site-header">
  <nav class="main-nav">
    <a href="#">HOME</a><span class="dot"></span>
    <a href="#">SHOP</a><span class="dot"></span>
    <a href="#">ABOUT US</a><span class="dot"></span>
    <a href="#">CONTACT US</a>
  </nav>
  <div class="brand">RIMU VALE HONEY</div>
  <svg class="cart" width="24" height="24" viewBox="0 0 24 24" fill="none" stroke="#ccc" stroke-width="1.6"><path d="M2 3h3l3 12h11l2-8H6"/><circle cx="9" cy="20" r="1.6"/><circle cx="18" cy="20" r="1.6"/></svg>
</header>

<section class="hero">
  <svg class="abs" style="left:0;top:0" width="1200" height="690" viewBox="0 0 1200 690">
    <defs>
      <linearGradient id="heroSky" x1="0" y1="0" x2="0" y2="1">
        <stop offset="0" stop-color="#7fa7c9"/>
        <stop offset=".32" stop-color="#5c5a48"/>
        <stop offset=".62" stop-color="#b8862f"/>
        <stop offset="1" stop-color="#d9a94e"/>
      </linearGradient>
    </defs>
    <polygon role="img" aria-label="Snow-capped mountain above golden tussock grassland" points="0,0 1200,0 1200,524 600,682 0,524" fill="url(#heroSky)"/>
    <polygon points="0,524 600,682 600,690 0,534" fill="var(--gold)"/>
    <polygon points="600,682 1200,524 1200,528 600,686" fill="#ffffff"/>
    <path d="M66 284 l-12 12 12 12" fill="none" stroke="#fff" stroke-width="2"/>
    <path d="M1130 284 l12 12 -12 12" fill="none" stroke="#fff" stroke-width="2"/>
    <rect x="593" y="618" width="12" height="20" rx="6" fill="none" stroke="#fff" stroke-width="1.5"/>
  </svg>
  <h1 class="hero-title">THE WORLD’S MOST RARE &amp;<br>PRECIOUS MĀNUKA HONEY</h1>
  <p class="hero-text">Lorem ipsum dolor sit amet, consectetur adipiscing elit, sed do eiusmod tempor incididunt ut labore et dolore magna aliqua.</p>
  <a class="btn hero-btn" href="#">SHOP NOW</a>
  <div class="jar" role="img" aria-label="Blue jar of Mānuka honey" style="left:835px;top:262px;width:288px;height:290px;background:linear-gradient(180deg,#1b1b1b 0 18%,#1f4c9a 18% 82%,#1b1b1b 82%)"></div>
  <div class="jar" role="img" aria-label="Red jar of Mānuka honey" style="left:666px;top:308px;width:300px;height:300px;background:linear-gradient(180deg,#1b1b1b 0 20%,#c3183f 20% 80%,#1b1b1b 80%)"></div>
</section>

<h2 class="section-title" style="top:818px;font-size:32px">FEATURED MĀNUKA HONEY PRODUCTS</h2>

<div class="card" style="left:100px"><div class="name">KPS 5+ Mānuka Honey</div><div class="price">From $29.99</div><div class="stars">★★★★★</div></div>
<div class="card" style="left:438px"><div class="name">KPS 5+ Mānuka Honey</div><div class="price">From $97.99</div><div class="stars">★★★★★</div></div>
<div class="card" style="left:776px"><div class="name">KPS 5+ Mānuka Honey</div><div class="price">From $214.99</div><div class="stars">★★★★★</div></div>
<div class="jar" role="img" aria-label="Purple jar of Mānuka honey" style="left:172px;top:907px;width:175px;height:198px;background:linear-gradient(180deg,#1b1b1b 0 24%,#6a2a8e 24% 80%,#1b1b1b 80%)"></div>
<div class="jar" role="img" aria-label="Green jar of Mānuka honey" style="left:510px;top:907px;width:175px;height:198px;background:linear-gradient(180deg,#1b1b1b 0 24%,#1f7a3c 24% 80%,#1b1b1b 80%)"></div>
<div class="jar" role="img" aria-label="Black jar of Mānuka honey" style="left:846px;top:907px;width:175px;height:198px;background:linear-gradient(180deg,#1b1b1b 0 24%,#2b2b2b 24% 80%,#1b1b1b 80%)"></div>
<svg class="abs" style="left:58px;top:1100px" width="20" height="32"><path d="M16 2 L4 16 L16 30" fill="none" stroke="#333" stroke-width="2"/></svg>
<svg class="abs" style="left:1114px;top:1100px" width="20" height="32"><path d="M4 2 L16 16 L4 30" fill="none" stroke="#333" stroke-width="2"/></svg>
<a class="btn abs" href="#" style="left:476px;top:1269px;width:248px;height:44px">SHOP AL PRODUCTS</a>

<section class="abs" role="img" aria-label="Beekeepers in protective suits tending wooden hives" style="left:0;top:1412px;width:1200px;height:531px;background:linear-gradient(135deg,#4c4a33,#7a5a2c 45%,#a86f2a 70%,#3f4a2c)"></section>
<div class="abs" style="left:0;top:1585px;width:1200px;text-align:center;color:#fff;font-size:36px;font-weight:500">OUR STORY</div>
<div class="abs" style="left:0;top:1630px;width:1200px;text-align:center;color:#fff;font-size:19px">A family’s love affair with bees...</div>
<svg class="abs" style="left:556px;top:1665px" width="88" height="88"><circle cx="44" cy="44" r="42" fill="#fff" opacity=".35"/><circle cx="44" cy="44" r="34" fill="#fff"/><path d="M38 32 L56 44 L38 56Z" fill="#111"/></svg>

<h2 class="section-title" style="top:2026px;font-size:34px">WHAT IS MGO/KPS</h2>
<div class="abs" style="left:100px;top:2080px;width:1000px;height:1px;background:var(--line)"></div>
<div class="abs" style="left:548px;top:2078px;width:104px;height:4px;background:var(--gold)"></div>
<p class="abs" style="left:290px;top:2104px;width:620px;text-align:center;font-size:12.5px;line-height:22px;color:#222">Rimu Vale Honey Blends or Multifloral Rimu Vale Honey are generally cheaper and contain honey from the nectar of many flowers, or have been blended with other types of honey.</p>
<p class="abs" style="left:0;top:2160px;width:1200px;text-align:center;font-size:13px;font-weight:700;color:#111">Here’s how the KPS and MGO/MG ratings line up:</p>

<div class="abs" role="img" aria-label="Honey dripping from a wooden spoon over a jar" style="left:534px;top:2258px;width:666px;height:282px;background:linear-gradient(90deg,#5a2a12,#8e4a14 45%,#c57a1c 80%,#6e3812)"></div>
<div class="abs" style="left:644px;top:2306px;color:#fff;font-size:36px;line-height:44px;font-weight:400">Order Honey With<br>Experience!</div>
<p class="abs" style="left:645px;top:2408px;width:400px;color:#fff;font-size:16px;line-height:27px">Grab your friends and enjoy a tasting right here at Rimu Vale Honey Company</p>
<a class="btn abs" href="#" style="left:642px;top:2514px;width:157px;height:44px">SHOP NOW</a>

<svg class="abs" style="left:78px;top:2150px" width="500" height="500">
  <circle cx="246" cy="250" r="240" fill="#fff" stroke="var(--gold)" stroke-width="7"/>
</svg>
<div class="kps-table">
  <div class="abs" style="left:0;top:8px;font-size:14px">Strength</div>
  <div class="abs" style="left:114px;top:4px;font-size:17px;width:170px;text-align:center">MGO(antibacterial)*</div>
  <div class="abs" style="left:114px;top:26px;font-size:12px;width:170px;text-align:center">Suggested Usage</div>
  <div class="abs" style="left:332px;top:6px;font-size:14px">KPS**</div>
  <div class="kps-row rule" style="top:52px"><span class="lvl" style="top:2px">MILD</span><span class="use" style="top:4px">Every day</span><span class="mgo" style="top:2px">MGO 120+</span><span class="kps" style="top:0">7.5+</span></div>
  <div class="kps-row rule" style="top:97px"><span class="lvl" style="top:2px">MEDIUM</span><span class="use" style="top:4px">General Wellbeing</span><span class="mgo" style="top:2px">MGO 220+</span><span class="kps" style="top:0">10+</span></div>
  <div class="kps-row rule" style="top:141px"><span class="lvl" style="top:2px">HIGH</span><span class="use" style="top:4px">Digestive Health</span><span class="mgo" style="top:2px">MGO 400+</span><span class="kps" style="top:0">13+</span></div>
  <div class="kps-row" style="top:186px"><span class="lvl" style="top:2px">ULTRA-HIGH</span><span class="use" style="top:2px">Wound Care &amp;<br>Digestive Health</span><span class="mgo" style="top:2px">MGO 900+</span><span class="kps" style="top:0">25+</span></div>
</div>

<svg class="abs" style="left:333px;top:2712px" width="48" height="48"><circle cx="24" cy="24" r="20" fill="none" stroke="var(--gold)" stroke-width="2"/></svg>
<h3 class="abs" style="left:110px;top:2786px;width:445px;text-align:center;font-size:30px;font-weight:500;color:var(--ink)">ABOUT Rimu Vale Honey</h3>
<p class="abs" style="left:110px;top:2834px;width:445px;text-align:justify;text-align-last:center;font-size:14px;line-height:24px;color:#444">Lorem ipsum dolor sit amet, consectetur adipiscing elit, sed do eiusmod tempor incididunt ut laboolore magna aliqua. Quis ipsum suspendisse ultrices gravida. Risus commodo viverra maecenas accumsan Lorem ipsum dolor sit amet, consectetur</p>
<a class="btn abs" href="#" style="left:278px;top:2953px;width:155px;height:43px">LEARN MORE</a>
<div class="abs" style="left:641px;top:2687px;width:428px;height:313px;border:2px solid var(--gold)"></div>
<div class="abs" role="img" aria-label="Mountain and winding road beside a spoon of honey over a jar" style="left:622px;top:2704px;width:429px;height:314px;background:linear-gradient(180deg,#4f8fd0 0 38%,#6b8a4a 38% 70%,#c98a1e 70%)"></div>
<div class="abs" style="left:1076px;top:2760px;writing-mode:vertical-rl;font-size:9px;letter-spacing:4px;color:var(--gold)">ABOUT RIMU VALE HONEY</div>

<h2 class="section-title" style="top:3164px;font-size:33px">SIGN UP FOR OUR NEWSLETTER</h2>
<p class="abs" style="left:0;top:3210px;width:1200px;text-align:center;font-size:17px;color:#333">Lorem ipsum dolor sit amet, consectetur adipiscing elit, sed</p>
<form class="abs" style="left:319px;top:3265px;width:561px;height:54px;border:1px solid #ccc;border-radius:27px;background:#fff">
  <span class="abs" style="left:24px;top:17px;font-size:15px;color:#333">Enter Your Email address</span>
  <span class="btn abs" style="left:420px;top:2px;width:138px;height:48px;border-radius:24px;font-size:16px">SUBSCRIBE</span>
</form>

<footer>
  <div class="abs" style="left:0;top:-1px;width:1200px;height:2px;background:#cfcfcf"></div>
  <svg class="abs" style="left:532px;top:-68px" width="136" height="136"><circle cx="68" cy="68" r="64" fill="var(--footer)" stroke="#cfcfcf" stroke-width="2"/><circle cx="68" cy="68" r="54" fill="none" stroke="var(--gold)" stroke-width="1.5"/></svg>
  <div class="abs" style="left:532px;top:-8px;width:136px;text-align:center;color:var(--gold);font-size:11px;font-weight:500;letter-spacing:1px">RIMU VALE HONEY</div>
  <nav class="foot-nav">
    <a href="#" style="left:296px">HOME</a>
    <a href="#" style="left:398px">SHOP</a>
    <a href="#" style="left:515px">ABOUT US</a>
    <a href="#" style="left:626px">FAQ</a>
    <a href="#" style="left:738px">PARTNERS</a>
    <a href="#" style="left:880px">CONTACT US</a>
  </nav>
  <svg class="abs" style="left:538px;top:150px" width="124" height="16"><circle cx="8" cy="8" r="6" fill="#ddd"/><circle cx="42" cy="8" r="6" fill="#ddd"/><circle cx="76" cy="8" r="6" fill="#ddd"/><circle cx="110" cy="8" r="6" fill="#ddd"/></svg>
  <p class="abs" style="left:0;top:196px;width:1200px;text-align:center;color:#e6e6e6;font-size:14px">© 2021 Rimu Vale Honey Co. All Rights Reserved.</p>
</footer>

</body>
</html>
```